Boundless Volt Product design

We need a bottle design for our product. Boundless Volt is a Gaming Nootropic made to increase Energy, Focus, Reaction time, and Clarity of an eSport gamer. It will be 40 servings a bottle. Currently, all the ingredients haven't been finalized so after the competition is over we will have to work with the designer to also make an ingredients label for the back of it. For the flavor, we will call it tundra mist.

The attachments included:. The velvet outlaws picture as a font style I like for the logo.
The Z CHARGE REFRESH PICTURE IS WHAT WE WANT OUR DESIGN to look like something similar a clean and simple design that stands out!

Z Charge bottle is what our biggest competitors product looks like. The boundless volt picture as the current logo we are using but can be changed.

Overall the pictures are just some references for what I could possibly want the design to look like however, I'm open to your designer's ideas and concepts you think would make for a cool looking Gaming Nootropic product bottle design. I appreciate everyone working on this and look forward to seeing your designs have a great day!

Target Market(s)

Gamers between the ages of 18-30

Industry/Entity Type

Health And Wellness

Requirements
Must have
• Boundless Volt logo, state that it is for energy, focus, reaction, and clarity. state 40 serivngs. state flavor.

```html
<!DOCTYPE html>
<html lang="en">
<head>
<meta charset="utf-8">
<title>Boundless Volt – Tundra Mist Label</title>
<link href="https://fonts.googleapis.com/css2?family=Saira+Condensed:ital,wght@0,600;0,800;1,700;1,800&family=Open+Sans:wght@500&display=swap" rel="stylesheet">
<style>
  :root {
    --bg: #e6e7e9;
    --label-white: #ffffff;
    --brand-blue: #2a4fa5;
    --brand-blue-deep: #22449a;
    --pattern-blue: #a9cdea;
    --logo-grey: #4b4f55;
    --rule-grey: #a7a9ad;
    --text-white: #ffffff;
  }
  * { margin: 0; padding: 0; box-sizing: border-box; }
  html, body { width: 1200px; height: 1024px; overflow: hidden; background: var(--bg); }
  .canvas { position: relative; width: 1200px; height: 1024px; }

  .label {
    position: absolute; left: 40px; top: 110px; width: 1120px; height: 800px;
    background: var(--label-white); overflow: hidden;
  }
  .pattern-band {
    position: absolute; left: 0; top: 24px; width: 100%; height: 78px;
    background: linear-gradient(180deg, var(--pattern-blue) 0%, #cfe3f3 100%);
    opacity: .85;
  }
  .servings-tab {
    position: absolute; left: 870px; top: 0; width: 104px; height: 340px;
    background: var(--brand-blue); border-radius: 0 0 16px 16px;
    color: var(--text-white); text-align: center;
    display: flex; flex-direction: column; justify-content: flex-end; padding-bottom: 24px;
    font-family: "Saira Condensed", sans-serif;
  }
  .servings-tab .count { font-size: 70px; font-weight: 800; line-height: .95; }
  .servings-tab .unit { font-size: 26px; font-weight: 600; line-height: 1; }

  .brand-block { position: absolute; left: 240px; top: 150px; width: 600px; text-align: center; }
  .brand-name {
    font-family: "Saira Condensed", sans-serif; font-weight: 800;
    color: var(--logo-grey); font-size: 118px; line-height: .9; text-transform: uppercase;
    letter-spacing: 2px;
  }
  .brand-rule { width: 480px; height: 4px; background: var(--rule-grey); margin: 22px auto 14px; }
  .audience {
    font-family: "Saira Condensed", sans-serif; font-style: italic; font-weight: 700;
    color: var(--brand-blue); font-size: 50px; letter-spacing: 5px; line-height: 1;
  }

  .base-band {
    position: absolute; left: 0; top: 555px; width: 100%; height: 245px;
    background: var(--brand-blue);
  }
  .claims-strip {
    position: absolute; left: 240px; top: 555px; width: 420px; height: 82px;
    background: var(--label-white);
    clip-path: polygon(0 0, 100% 0, 97% 100%, 0 100%);
  }
  .zero-claims { position: absolute; left: 250px; top: 555px; display: flex; gap: 8px; }
  .zero-claim {
    width: 90px; height: 76px; background: var(--brand-blue-deep);
    transform: skewX(-10deg); color: var(--text-white); text-align: center;
    font-family: "Saira Condensed", sans-serif; font-style: italic;
  }
  .zero-claim .num { display: block; font-size: 50px; font-weight: 800; line-height: 1; padding-top: 4px; }
  .zero-claim .what { display: block; font-size: 15px; font-weight: 600; text-transform: uppercase; }
  .flavor {
    position: absolute; left: 690px; top: 568px;
    font-family: "Saira Condensed", sans-serif; font-style: italic; font-weight: 800;
    color: var(--text-white); font-size: 60px; letter-spacing: 4px; line-height: 1; text-transform: uppercase;
  }
  .benefits {
    position: absolute; left: 0; top: 665px; width: 100%; text-align: center;
    font-family: "Saira Condensed", sans-serif; font-weight: 800;
    color: var(--text-white); font-size: 48px; letter-spacing: 5px; text-transform: uppercase; line-height: 1;
  }
  .benefits .sep { margin: 0 14px; font-weight: 600; }
  .fine-print {
    position: absolute; left: 0; top: 735px; width: 100%; text-align: center;
    font-family: "Open Sans", sans-serif; font-weight: 500;
    color: var(--text-white); font-size: 21px; letter-spacing: .5px;
  }
</style>
</head>
<body>
<div class="canvas">
  <section class="label">
    <div class="pattern-band" role="img" aria-label="Light blue pixel checker pattern band"></div>

    <div class="servings-tab">
      <span class="count">40</span>
      <span class="unit">servings</span>
    </div>

    <div class="brand-block">
      <h1 class="brand-name">Boundless<br>Volt</h1>
      <div class="brand-rule"></div>
      <p class="audience">FOR E-SPORT GAMERS</p>
    </div>

    <div class="base-band"></div>
    <div class="claims-strip"></div>
    <div class="zero-claims">
      <div class="zero-claim"><span class="num">0</span><span class="what">Sugar</span></div>
      <div class="zero-claim"><span class="num">0</span><span class="what">Calories</span></div>
      <div class="zero-claim"><span class="num">0</span><span class="what">Caffeine</span></div>
    </div>
    <p class="flavor">Tundra Mist</p>

    <p class="benefits">Energy<span class="sep">|</span>Focus<span class="sep">|</span>Reaction<span class="sep">|</span>Clarity</p>
    <p class="fine-print">Dietary Supplement | Net Weight 12 OZ (118g)</p>
  </section>
</div>
</body>
</html>
```